Awesome photographers card for an awesome new business

Double sided business card Black background and silver logo in middle on one side. Details on otherside. please keep it simple

Industry/Entity Type

Photographer

Contact Information for Business Card

Gerald Fenwick
0452817360
GeraldFenwickPhotography47@mailbox.test
www.GeraldFenwickPhotography.test.au
Instagram _Gerald_fenwick

Requirements
Must have
• My logo in Silver
• please use instagram logo instead of "Instagram"

```html
<!DOCTYPE html>
<html lang="en">
<head>
<meta charset="utf-8">
<title>Gerald Fenwick Photography – Business Card</title>
<link href="https://fonts.googleapis.com/css2?family=Lato:wght@400;700&display=swap" rel="stylesheet">
<style>
  :root {
    --stage: #2b2b2b;
    --card: #050505;
    --silver: #d9d9d9;
    --silver-dim: #bdbdbd;
    --ghost: #161616;
  }
  * { margin: 0; padding: 0; box-sizing: border-box; }
  html, body { width: 1200px; height: 880px; overflow: hidden; }
  body {
    background: var(--stage);
    font-family: "Lato", Arial, sans-serif;
    color: var(--silver);
    position: relative;
  }
  .card {
    position: absolute;
    width: 600px;
    height: 343px;
    background: var(--card);
    box-shadow: 0 10px 30px rgba(0,0,0,0.55);
    overflow: hidden;
  }
  .card--front { left: 70px; top: 80px; }
  .card--back  { left: 530px; top: 457px; }

  /* Brand mark: plain circle beside the name */
  .brand {
    position: absolute;
    display: flex;
    align-items: center;
    gap: 12px;
  }
  .brand__circle {
    border: 2px solid var(--silver);
    border-radius: 50%;
    flex: none;
  }
  .brand__name {
    font-weight: 400;
    color: var(--silver);
    letter-spacing: 3px;
    text-transform: uppercase;
    white-space: nowrap;
  }
  .card--front .brand { left: 50%; top: 95px; transform: translateX(-50%); }
  .card--front .brand__circle { width: 44px; height: 44px; }
  .card--front .brand__name { font-size: 24px; }

  .card--back .brand { right: 32px; top: 34px; gap: 9px; }
  .card--back .brand__circle { width: 30px; height: 30px; }
  .card--back .brand__name { font-size: 16px; letter-spacing: 2px; }

  .front__url {
    position: absolute;
    left: 0; right: 0;
    bottom: 52px;
    text-align: center;
    font-size: 16px;
    color: var(--silver);
  }

  .back__ghost-name {
    position: absolute;
    left: 40px;
    top: 70px;
    font-size: 64px;
    font-weight: 700;
    color: var(--ghost);
    letter-spacing: 2px;
    white-space: nowrap;
  }

  .contact {
    position: absolute;
    left: 40px;
    bottom: 34px;
  }
  .contact__name {
    font-size: 20px;
    font-weight: 700;
    letter-spacing: 0.5px;
    text-transform: uppercase;
    margin-bottom: 10px;
  }
  .contact__list { list-style: none; }
  .contact__item {
    display: flex;
    align-items: center;
    gap: 8px;
    font-size: 15px;
    line-height: 22px;
    color: var(--silver);
  }
  .contact__icon {
    width: 16px; height: 16px;
    flex: none;
  }
  .contact__url {
    margin-top: 10px;
    font-size: 15px;
    color: var(--silver-dim);
  }
</style>
</head>
<body>

  <section class="card card--front" aria-label="Card front">
    <div class="brand">
      <span class="brand__circle"></span>
      <span class="brand__name">Gerald Fenwick</span>
    </div>
    <p class="front__url">www.GeraldFenwickPhotography.test.au</p>
  </section>

  <section class="card card--back" aria-label="Card back">
    <div class="back__ghost-name" aria-hidden="true">Gerald Fenwick</div>

    <div class="brand">
      <span class="brand__circle"></span>
      <span class="brand__name">Gerald Fenwick</span>
    </div>

    <div class="contact">
      <h1 class="contact__name">Gerald Fenwick</h1>
      <ul class="contact__list">
        <li class="contact__item">
          <svg class="contact__icon" viewBox="0 0 16 16" aria-hidden="true">
            <circle cx="8" cy="8" r="7.2" fill="none" stroke="#d9d9d9" stroke-width="1.2"/>
            <path d="M5.4 4.4 L6.8 4.2 L7.4 6.2 L6.6 6.9 Q7.4 8.6 9.1 9.4 L9.8 8.6 L11.8 9.2 L11.6 10.6 Q8.6 11.4 6 8.6 Q4.6 6.6 5.4 4.4 Z" fill="#d9d9d9"/>
          </svg>
          <span>0452817360</span>
        </li>
        <li class="contact__item">
          <svg class="contact__icon" viewBox="0 0 16 16" aria-hidden="true">
            <circle cx="8" cy="8" r="7.2" fill="none" stroke="#d9d9d9" stroke-width="1.2"/>
            <rect x="4.2" y="5.3" width="7.6" height="5.4" fill="none" stroke="#d9d9d9" stroke-width="1"/>
            <path d="M4.2 5.3 L8 8.3 L11.8 5.3" fill="none" stroke="#d9d9d9" stroke-width="1"/>
          </svg>
          <span>GeraldFenwickPhotography47@mailbox.test</span>
        </li>
        <li class="contact__item">
          <svg class="contact__icon" viewBox="0 0 16 16" aria-hidden="true">
            <circle cx="8" cy="8" r="7.2" fill="none" stroke="#d9d9d9" stroke-width="1.2"/>
          </svg>
          <span>_Gerald_fenwick</span>
        </li>
      </ul>
      <p class="contact__url">www.GeraldFenwickPhotography.test.au</p>
    </div>
  </section>

</body>
</html>
```